Ferncliff Capital - Website Design

We need a website design for a new commercial real estate company called Ferncliff Capital. We're effectively commercial mortgage brokers connecting real estate investors to lenders. We need a website that is simple (not busy), elegant, professional, and user-friendly. A lot of the users will be in their 50's and less tech savvy, so a stream-lined design is best. The website will serve as a portal for lenders to review new financing opportunities, as well as for real estate investors to review terms from lenders.
Updates
Just uploaded our logo.
Target Market(s)
Commercial real estate investors and lenders
Industry/Entity Type
Real Estate
Number of Pages Required
1 page
Colors
Designer to choose colors to be used in the design.
Look and feel

```html
<!DOCTYPE html>
<html lang="en">
<head>
<meta charset="utf-8">
<title>Ferncliff Capital</title>
<link rel="stylesheet" href="https://fonts.googleapis.com/css2?family=Montserrat:wght@600;700&family=Questrial&family=Open+Sans:wght@400&display=swap">
<style>
:root{
  --navy:#2e3d5f;
  --navy-deep:#2f3e63;
  --ink:#333a4a;
  --muted:#5d6270;
  --line:#d9dce3;
  --white:#ffffff;
  --hero-a:#c9ccd2;
  --hero-b:#9aa0a9;
  --band-a:#6f7e9c;
  --band-b:#44567d;
}
*{margin:0;padding:0;box-sizing:border-box}
html,body{width:1200px;height:2347px;overflow:hidden;background:var(--white)}
body{position:relative;font-family:"Questrial",sans-serif;color:var(--ink)}
.abs{position:absolute}

.site-header{position:absolute;left:0;top:0;width:1200px;height:113px;background:var(--white);box-shadow:0 2px 6px rgba(0,0,0,.18);z-index:3}
.brand{position:absolute;left:99px;top:34px;text-align:center;color:var(--navy);font-family:"Montserrat",sans-serif;font-weight:700}
.brand-name{font-size:33px;letter-spacing:1px;line-height:34px}
.brand-sub{font-size:15px;letter-spacing:1px;line-height:18px}
.main-nav a{position:absolute;top:54px;font-size:14px;color:var(--ink);text-decoration:none;letter-spacing:.3px}
.main-nav a.active{border-bottom:2px solid var(--navy);padding-bottom:8px}

.hero{position:absolute;left:0;top:113px;width:1200px;height:646px;overflow:hidden}
.hero-photo{position:absolute;inset:0;background:linear-gradient(100deg,var(--hero-a) 0%,#b7bcc4 45%,var(--hero-b) 100%)}
.hero-curve{position:absolute;left:0;bottom:0}
.hero-title{position:absolute;left:0;top:225px;width:1200px;text-align:center;font-family:"Montserrat",sans-serif;font-weight:700;font-size:74px;color:var(--white);letter-spacing:1px}
.hero-tagline{position:absolute;left:0;top:309px;width:1200px;text-align:center;font-size:20px;color:var(--white)}
.hero-arrow{position:absolute;top:280px}

.intro h2{position:absolute;left:0;top:790px;width:1200px;text-align:center;font-size:35px;font-weight:400;color:var(--navy)}
.intro p{position:absolute;left:125px;width:950px;text-align:center;font-family:"Open Sans",sans-serif;font-size:13.5px;line-height:26px;color:var(--muted)}

.about-band{position:absolute;left:0;top:1103px;width:1200px;height:375px;background:linear-gradient(120deg,var(--band-a),var(--band-b))}
.about-band h2{position:absolute;left:0;top:55px;width:1200px;text-align:center;font-size:56px;font-weight:400;color:var(--white)}
.about-band p{position:absolute;left:150px;top:142px;width:900px;text-align:center;font-family:"Open Sans",sans-serif;font-size:14.5px;line-height:23px;color:var(--white)}
.btn-outline-light{position:absolute;left:493px;top:249px;width:213px;height:49px;border:2px solid var(--white);color:var(--white);font-family:"Montserrat",sans-serif;font-weight:600;font-size:18px;line-height:45px;text-align:center}

.services h2{position:absolute;left:0;top:1545px;width:1200px;text-align:center;font-size:34px;font-weight:400;color:var(--ink)}
.service{position:absolute;top:1640px;width:250px;text-align:center}
.service-icon{display:block;margin:0 auto}
.service h3{margin-top:16px;font-size:17px;font-weight:400;letter-spacing:.5px;color:#222}
.service p{margin-top:8px;padding:0 18px;font-family:"Open Sans",sans-serif;font-size:12px;line-height:20px;color:var(--muted)}
.btn-outline{display:inline-block;margin-top:14px;width:130px;height:39px;border:2px solid var(--navy);font-size:15px;line-height:35px;color:var(--navy)}

.site-footer{position:absolute;left:0;top:2004px;width:1200px;height:343px;background:var(--navy-deep);color:var(--white)}
.site-footer h4{position:absolute;top:46px;font-size:18px;font-weight:400;letter-spacing:.5px}
.site-footer .link{position:absolute;font-size:14px;color:#d6dbe7}
.footer-divider{position:absolute;top:40px;width:1px;height:210px;background:rgba(255,255,255,.15)}
.contact-line{position:absolute;left:487px;font-size:14px;line-height:25px;color:#d6dbe7}
.newsletter-input{position:absolute;left:776px;top:114px;width:219px;height:38px;background:var(--white);color:#a9aebb;font-size:13px;line-height:38px;padding-left:14px;letter-spacing:.5px}
.newsletter-btn{position:absolute;left:995px;top:114px;width:106px;height:38px;background:#243150;font-size:14px;line-height:38px;text-align:center}
.social{position:absolute;top:167px;width:38px;height:38px;border-radius:50%;background:var(--white)}
.footer-rule{position:absolute;left:99px;top:272px;width:1002px;height:1px;background:rgba(255,255,255,.45)}
.copyright{position:absolute;left:99px;top:294px;font-size:13.5px;color:#d6dbe7}
</style>
</head>
<body>

<header class="site-header">
  <div class="brand"><div class="brand-name">FERNCLIFF</div><div class="brand-sub">CAPITAL</div></div>
  <nav class="main-nav">
    <a class="active" style="left:524px">HOME</a>
    <a style="left:604px">ABOUT US</a>
    <a style="left:702px">OUR SERVICES</a>
    <a style="left:834px">MORTGAGE BROKERS</a>
    <a style="left:1015px">CONTACT US</a>
  </nav>
</header>

<section class="hero">
  <div class="hero-photo" role="img" aria-label="Photo of a relaxed businessman at an office desk with a city skyline behind the window"></div>
  <svg class="hero-arrow" style="left:30px" width="20" height="36" viewBox="0 0 20 36"><path d="M17 2 L3 18 L17 34" fill="none" stroke="rgba(255,255,255,.7)" stroke-width="2"/></svg>
  <svg class="hero-arrow" style="left:1144px" width="20" height="36" viewBox="0 0 20 36"><path d="M3 2 L17 18 L3 34" fill="none" stroke="rgba(255,255,255,.7)" stroke-width="2"/></svg>
  <h1 class="hero-title">FERNCLIFF CAPITAL</h1>
  <p class="hero-tagline">We're effectively commercial mortgage brokers connecting real estate investors to lenders.</p>
  <svg class="hero-curve" width="1200" height="70" viewBox="0 0 1200 70"><path d="M0 70 L0 60 Q600 -50 1200 60 L1200 70 Z" fill="#ffffff"/></svg>
</section>

<section class="intro">
  <h2>We are a new Commercial Real Estate Company</h2>
  <p style="top:847px">Lorem ipsum dolor sit amet, consectetur adipiscing elit, sed do eiusmod tempor incididunt ut labore et dolore magna aliqua. Ut enim ad minim veniam, quis nostrud exercitation ullamco laboris nisi ut aliquip ex ea commodo consequat. Duis aute irure dolor in reprehenderit in voluptate velit esse cillum dolore eu fugiat nulla pariatur.</p>
  <p style="top:949px">Neque porro quisquam est, qui dolorem ipsum quia dolor sit amet, consectetur, adipisci velit, sed quia non numquam eius modi tempora incidunt ut labore et dolore magnam aliquam quaerat voluptatem. Ut enim ad minima veniam.</p>
</section>

<section class="about-band" role="img" aria-label="Photo of glass office towers tinted in navy blue">
  <h2>About Ferncliff Capital</h2>
  <p>At vero eos et accusamus et iusto odio dignissimos ducimus qui blanditiis praesentium voluptatum deleniti atque corrupti quos dolores et quas molestias excepturi sint occaecati cupiditate non provident, similique sunt in culpa qui officia deserunt mollitia animi, id est laborum et dolorum fuga. Et harum quidem rerum facilis est et expedita distinctio.</p>
  <div class="btn-outline-light">LEARN MORE</div>
</section>

<section class="services">
  <h2>Our Services</h2>

  <div class="service" style="left:78px">
    <svg class="service-icon" width="122" height="122" viewBox="0 0 122 122"><circle cx="61" cy="61" r="60" fill="#ffffff" stroke="var(--navy)" stroke-width="2"/><circle cx="61" cy="61" r="55" fill="var(--navy)"/>
      <g fill="none" stroke="#fff" stroke-width="3" stroke-linejoin="round"><path d="M62 44 H46 a4 4 0 0 0 -4 4 V76 a4 4 0 0 0 4 4 H72 a4 4 0 0 0 4 -4 V62"/><path d="M74 40 L82 48 L62 68 L53 70 L55 61 Z"/></g></svg>
    <h3>FREE REGISTRATION</h3>
    <p>Sed ut perspiciatis unde omnis iste natus error sit voluptatem accusantium doloremque laudantium.</p>
    <div class="btn-outline">READ MORE</div>
  </div>

  <div class="service" style="left:343px">
    <svg class="service-icon" width="122" height="122" viewBox="0 0 122 122"><circle cx="61" cy="61" r="60" fill="#ffffff" stroke="var(--navy)" stroke-width="2"/><circle cx="61" cy="61" r="55" fill="var(--navy)"/>
      <g fill="none" stroke="#fff" stroke-width="2.6" stroke-linejoin="round"><rect x="46" y="44" width="30" height="38" rx="2"/><rect x="54" y="40" width="14" height="7" rx="1"/><path d="M52 56 H70 M52 63 H70 M52 70 H62"/><circle cx="72" cy="76" r="6"/><path d="M69 76 l2 2 l4 -4"/></g></svg>
    <h3>PROPERTY APPRAISAL</h3>
    <p>Sed ut perspiciatis unde omnis iste natus error sit voluptatem accusantium doloremque laudantium.</p>
    <div class="btn-outline">READ MORE</div>
  </div>

  <div class="service" style="left:606px">
    <svg class="service-icon" width="122" height="122" viewBox="0 0 122 122"><circle cx="61" cy="61" r="60" fill="#ffffff" stroke="var(--navy)" stroke-width="2"/><circle cx="61" cy="61" r="55" fill="var(--navy)"/>
      <path d="M61 38 a14 14 0 0 1 14 14 c0 10 -14 28 -14 28 s-14 -18 -14 -28 a14 14 0 0 1 14 -14 Z" fill="#fff"/><circle cx="61" cy="52" r="5" fill="var(--navy)"/></svg>
    <h3>LARGE COVERAGE</h3>
    <p>Sed ut perspiciatis unde omnis iste natus error sit voluptatem accusantium doloremque laudantium.</p>
    <div class="btn-outline">READ MORE</div>
  </div>

  <div class="service" style="left:870px">
    <svg class="service-icon" width="122" height="122" viewBox="0 0 122 122"><circle cx="61" cy="61" r="60" fill="#ffffff" stroke="var(--navy)" stroke-width="2"/><circle cx="61" cy="61" r="55" fill="var(--navy)"/>
      <g fill="none" stroke="#fff" stroke-width="2.6" stroke-linejoin="round"><path d="M38 60 L61 40 L84 60"/><path d="M44 56 V82 H78 V56"/><rect x="55" y="66" width="12" height="16"/><rect x="48" y="60" width="8" height="7"/><rect x="66" y="60" width="8" height="7"/></g></svg>
    <h3>SELECTING A HOUSE</h3>
    <p>Sed ut perspiciatis unde omnis iste natus error sit voluptatem accusantium doloremque laudantium.</p>
    <div class="btn-outline">READ MORE</div>
  </div>
</section>

<footer class="site-footer">
  <h4 style="left:99px">QUICK LINKS</h4>
  <span class="link" style="left:99px;top:86px">Home</span>
  <span class="link" style="left:99px;top:117px">About Us</span>
  <span class="link" style="left:99px;top:149px">Our Services</span>
  <span class="link" style="left:99px;top:180px">Mortgage Brokers</span>
  <span class="link" style="left:280px;top:86px">Terms of Service</span>
  <span class="link" style="left:280px;top:117px">Privacy Policy</span>
  <span class="link" style="left:280px;top:149px">Contact Us</span>

  <div class="footer-divider" style="left:426px"></div>
  <h4 style="left:487px">CONTACT INFO</h4>
  <div class="contact-line" style="top:81px">Ferncliff Capital , City<br>Name , Country Code.</div>
  <div class="contact-line" style="top:138px">
    <svg width="13" height="13" viewBox="0 0 24 24" style="vertical-align:-1px;margin-right:12px"><path fill="#fff" d="M6.6 10.8a15 15 0 0 0 6.6 6.6l2.2-2.2a1 1 0 0 1 1-.25 11.4 11.4 0 0 0 3.6.57 1 1 0 0 1 1 1V20a1 1 0 0 1-1 1A17 17 0 0 1 3 4a1 1 0 0 1 1-1h3.5a1 1 0 0 1 1 1c0 1.25.2 2.45.57 3.6a1 1 0 0 1-.25 1z"/></svg>+00 123 45 67 890</div>
  <div class="contact-line" style="top:170px">
    <svg width="14" height="11" viewBox="0 0 24 18" style="vertical-align:0;margin-right:12px"><rect width="24" height="18" rx="2" fill="#fff"/><path d="M1 2 L12 10 L23 2" fill="none" stroke="var(--navy-deep)" stroke-width="2"/></svg>info@domainname.com</div>

  <div class="footer-divider" style="left:727px"></div>
  <h4 style="left:773px">SIGN UP FOR NEWSLETTERS</h4>
  <span class="link" style="left:775px;top:84px;font-size:13.5px">Please sign up here for latest news</span>
  <div class="newsletter-input">EMAIL ADDRESS</div>
  <div class="newsletter-btn">SUBSCRIBE</div>
  <span class="social" style="left:776px" aria-label="Social link"></span>
  <span class="social" style="left:824px" aria-label="Social link"></span>
  <span class="social" style="left:873px" aria-label="Social link"></span>
  <span class="social" style="left:921px" aria-label="Social link"></span>

  <div class="footer-rule"></div>
  <div class="copyright">© 2017 FERNCLIFF CAPITAL.&nbsp; All right reserved . Term of Use</div>
</footer>

</body>
</html>
```